Corporate Template

Looking for a set of corporate slides to be made which contain multiple different slides and orientations. Looking for at least 8 to 10 different master pages plus a Coversheet and closeout page. Incorporating a color palate similar to our logo coloring is preferred.
I have attached a logo.
I like the amber quill works designs best so far. They seem to fit what I'm looking for in terms of visual appearance.
Reason: I'm trying to allow time for a couple new designers to incorporate some changes I requested to their existing designs.

```html
<!DOCTYPE html>
<html lang="en">
<head>
<meta charset="utf-8">
<title>Halcyon – Corporate Slide Template</title>
<link rel="stylesheet" href="https://fonts.googleapis.com/css2?family=Arimo:ital,wght@0,400;0,700;1,400&display=swap">
<style>
  :root {
    --navy: #0b3f80;
    --navy-deep: #072d63;
    --blue: #1462ad;
    --logo-blue: #1f78c1;
    --cyan: #3fb2e6;
    --sky: #5fcaf3;
    --green: #a2c35e;
    --purple: #9b87bb;
    --ink: #143a6e;
    --text: #5a6470;
    --page: #eef1f5;
    --white: #ffffff;
  }
  * { box-sizing: border-box; margin: 0; padding: 0; }
  html, body { width: 1200px; height: 896px; overflow: hidden; }
  body {
    background: var(--page);
    font-family: "Arimo", Arial, sans-serif;
    color: var(--text);
    position: relative;
  }
  .slide {
    position: absolute;
    width: 366px;
    height: 276px;
    background: var(--white);
    overflow: hidden;
    box-shadow: 0 0 0 1px #dde3ea;
  }
  .col-1 { left: 30px; } .col-2 { left: 408px; } .col-3 { left: 792px; }
  .row-1 { top: 22px; } .row-2 { top: 304px; } .row-3 { top: 586px; }

  .slide-header {
    position: absolute; left: 0; top: 0; width: 100%; height: 34px;
    background: var(--navy);
    color: var(--white);
    font-size: 12.5px;
    padding: 11px 0 0 20px;
  }
  .brand-box {
    position: absolute; right: 0; top: 0; width: 62px; height: 34px;
    background: var(--logo-blue);
    color: var(--white);
    font-weight: 700;
    font-size: 10px;
    letter-spacing: 0.3px;
    display: flex; align-items: center; justify-content: center;
  }

  .slide-footer {
    position: absolute; left: 0; bottom: 0; width: 100%; height: 18px;
    background: var(--navy);
    font-size: 6.5px;
    display: flex; align-items: center;
    padding-left: 14px;
  }
  .slide-footer .deck-title { color: var(--cyan); padding-right: 10px; border-right: 1px solid var(--cyan); }
  .slide-footer .deck-sub { color: var(--white); font-weight: 700; padding-left: 10px; }
  .slide-footer .page-no {
    position: absolute; right: 0; top: 0; width: 16px; height: 18px;
    background: var(--logo-blue); color: var(--white);
    text-align: center; line-height: 18px; font-size: 6px;
  }

  .heading { color: var(--ink); font-weight: 700; font-size: 8px; text-transform: uppercase; }
  .sub { color: var(--cyan); font-size: 7px; margin: 2px 0 6px; }
  .body { font-size: 5.2px; line-height: 1.45; color: var(--text); }
  .note {
    color: var(--cyan); font-style: italic; font-size: 7px;
    border-top: 1px solid var(--cyan); border-bottom: 1px solid var(--cyan);
    padding: 4px 0; margin: 6px 0;
  }
  .bullets { list-style: none; }
  .bullets li { display: flex; gap: 5px; align-items: flex-start; margin-bottom: 5px; }
  .bullet-icon { flex: 0 0 9px; width: 9px; height: 9px; }

  .picture-box { background: var(--navy); display: flex; align-items: center; justify-content: center; }
  .picture-box svg { width: 36%; height: auto; }

  /* cover */
  .cover-art {
    position: absolute; inset: 0;
    background: radial-gradient(ellipse at 28% 35%, #3a8de0 0%, #1560b8 35%, #0a3f8c 70%, #072f6e 100%);
  }
  .cover-titles { position: absolute; right: 20px; top: 132px; text-align: right; color: var(--white); }
  .cover-titles .kicker { color: var(--sky); font-size: 9px; letter-spacing: 0.3px; }
  .cover-titles .title { font-size: 14px; font-weight: 700; margin-top: 3px; }
  .cover-titles .subtitle { font-size: 11px; font-weight: 700; margin-top: 2px; }
  .cover-footer {
    position: absolute; left: 0; bottom: 0; width: 100%; height: 38px;
    background: rgba(7, 45, 99, 0.55);
    padding: 7px 0 0 26px;
    color: var(--sky); font-size: 7.5px; line-height: 1.45;
  }
  .cover-footer::before { content: ""; position: absolute; left: 14px; top: 7px; width: 1px; height: 22px; background: var(--cyan); }
  .cover .brand-box { top: auto; bottom: 0; height: 38px; }

  /* agenda */
  .agenda { position: absolute; left: 26px; top: 56px; width: 316px; }
  .agenda-group { margin-bottom: 12px; }
  .agenda-group .heading { font-size: 7.5px; margin-bottom: 3px; }
  .agenda-row { display: flex; align-items: center; font-size: 7px; color: var(--ink); height: 11.5px; }
  .agenda-row .bullet-icon { margin-right: 5px; }
  .agenda-row .leader { flex: 1; border-bottom: 1px dotted #8da3bf; margin: 0 6px; height: 6px; }
  .agenda-row .num { font-size: 6px; }

  /* overview */
  .overview-pic { position: absolute; left: 28px; top: 60px; width: 146px; height: 176px; }
  .overview-text { position: absolute; left: 196px; top: 60px; width: 150px; }
  .overview-text .heading { margin-bottom: 4px; }
  .overview-text .bullets { margin-top: 12px; }
  .overview-text .bullets li { margin-bottom: 12px; }

  /* team */
  .team { position: absolute; left: 25px; top: 64px; display: flex; gap: 30px; }
  .member { width: 86px; text-align: center; }
  .member .picture-box { width: 68px; height: 68px; margin: 0 auto 26px; }
  .member .heading { font-size: 7.5px; }
  .member .role { color: var(--cyan); font-size: 7px; margin: 1px 0 5px; }
  .member .body { text-align: left; }

  /* columns */
  .two-col { position: absolute; left: 28px; top: 54px; width: 316px; display: flex; gap: 22px; }
  .two-col > div { flex: 1; }
  .two-col .sub { margin-top: 6px; }
  .one-col { position: absolute; left: 28px; top: 54px; width: 314px; }

  /* chart */
  .chart { position: absolute; left: 22px; top: 66px; width: 136px; height: 136px; }
  .legend { position: absolute; left: 196px; top: 62px; width: 150px; list-style: none; }
  .legend li { position: relative; padding-left: 14px; margin-bottom: 14px; }
  .legend .swatch { position: absolute; left: 0; top: 2px; width: 5px; height: 5px; }
  .legend .series { color: var(--cyan); font-size: 6.5px; margin-bottom: 4px; }

  /* testimonial */
  .testimonial-main { position: absolute; left: 26px; top: 64px; width: 144px; }
  .testimonial-main .picture-box { width: 144px; height: 82px; margin-bottom: 7px; }
  .testimonial-main .heading { margin-bottom: 4px; }
  .testimonial-list { position: absolute; left: 200px; top: 64px; width: 150px; }
  .testimonial-item { display: flex; gap: 8px; margin-bottom: 18px; height: 48px; }
  .testimonial-item .picture-box { flex: 0 0 48px; height: 38px; }
  .testimonial-item .heading { font-size: 7.5px; }
  .testimonial-item .role { color: var(--cyan); font-size: 7px; margin-bottom: 2px; }

  /* closing */
  .closing-art {
    position: absolute; inset: 0;
    background: radial-gradient(ellipse at 70% 40%, #2a84d8 0%, #145db3 40%, #0a3d88 75%, #07306f 100%);
  }
  .closing-brand {
    position: absolute; left: 0; right: 0; top: 100px; text-align: center;
    color: var(--white); font-weight: 700; font-size: 34px; letter-spacing: 0.5px; line-height: 1;
  }
  .closing-contact {
    position: absolute; left: 162px; top: 218px;
    font-size: 6.5px; line-height: 1.9; color: var(--white);
  }
  .closing-contact .web { font-weight: 700; }
  .closing-contact .mail { color: var(--sky); }
  .closing-thanks { position: absolute; left: 20px; top: 232px; color: var(--sky); font-size: 7.5px; font-weight: 700; line-height: 1.1; }
  .closing-divider { position: absolute; left: 150px; top: 218px; width: 1px; height: 42px; background: var(--cyan); }
</style>
</head>
<body>

<svg width="0" height="0" style="position:absolute" aria-hidden="true">
  <defs>
    <symbol id="icon-image" viewBox="0 0 40 32">
      <rect x="2" y="2" width="36" height="28" fill="none" stroke="#3fb2e6" stroke-width="2.5"/>
      <circle cx="12" cy="11" r="3.5" fill="#3fb2e6"/>
      <path d="M6 26 L16 16 L22 21 L28 13 L35 26 Z" fill="#3fb2e6"/>
    </symbol>
    <symbol id="icon-bullet" viewBox="0 0 10 10">
      <circle cx="5" cy="5" r="4.3" fill="none" stroke="#1462ad" stroke-width="1"/>
      <circle cx="5" cy="5" r="2.8" fill="#3fb2e6"/>
      <path d="M4.2 3.4 L6 5 L4.2 6.6" fill="none" stroke="#ffffff" stroke-width="0.9"/>
    </symbol>
  </defs>
</svg>

<!-- 1 cover -->
<section class="slide cover col-1 row-1">
  <div class="cover-art" role="img" aria-label="Blue abstract background with a glowing profile of a human head and brain"></div>
  <div class="cover-titles">
    <p class="kicker">COMPANY PRESENTATION</p>
    <h1 class="title">PRESENTATION TITLE</h1>
    <p class="subtitle">Presentation Subtitle</p>
  </div>
  <div class="cover-footer">
    <p>COMPANY PRESENTATION</p>
    <p>November 2013</p>
  </div>
  <div class="brand-box">HALCYON</div>
</section>

<!-- 2 agenda -->
<section class="slide col-2 row-1">
  <header class="slide-header">Today's agenda</header>
  <div class="brand-box">HALCYON</div>
  <div class="agenda">
    <div class="agenda-group">
      <p class="heading">Topic title</p>
      <div class="agenda-row"><svg class="bullet-icon"><use href="#icon-bullet"/></svg>Topic Subtitle<span class="leader"></span><span class="num">#</span></div>
      <div class="agenda-row"><svg class="bullet-icon"><use href="#icon-bullet"/></svg>Topic Subtitle<span class="leader"></span><span class="num">#</span></div>
      <div class="agenda-row"><svg class="bullet-icon"><use href="#icon-bullet"/></svg>Topic Subtitle<span class="leader"></span><span class="num">#</span></div>
    </div>
    <div class="agenda-group">
      <p class="heading">Topic title</p>
      <div class="agenda-row"><svg class="bullet-icon"><use href="#icon-bullet"/></svg>Topic Subtitle<span class="leader"></span><span class="num">#</span></div>
      <div class="agenda-row"><svg class="bullet-icon"><use href="#icon-bullet"/></svg>Topic Subtitle<span class="leader"></span><span class="num">#</span></div>
    </div>
    <div class="agenda-group">
      <p class="heading">Topic title</p>
      <div class="agenda-row"><svg class="bullet-icon"><use href="#icon-bullet"/></svg>Topic Subtitle<span class="leader"></span><span class="num">#</span></div>
      <div class="agenda-row"><svg class="bullet-icon"><use href="#icon-bullet"/></svg>Topic Subtitle<span class="leader"></span><span class="num">#</span></div>
      <div class="agenda-row"><svg class="bullet-icon"><use href="#icon-bullet"/></svg>Topic Subtitle<span class="leader"></span><span class="num">#</span></div>
    </div>
  </div>
  <footer class="slide-footer"><span class="deck-title">PRESENTATION TITLE</span><span class="deck-sub">Presentation Subtitle</span><span class="page-no">1</span></footer>
</section>

<!-- 3 company overview -->
<section class="slide col-3 row-1">
  <header class="slide-header">Company overview</header>
  <div class="brand-box">HALCYON</div>
  <div class="overview-pic picture-box" role="img" aria-label="Company photo placeholder"><svg viewBox="0 0 40 32"><use href="#icon-image"/></svg></div>
  <div class="overview-text">
    <p class="heading">Company name</p>
    <p class="body">Lorem ipsum dolor sit amet, consectetur adipiscing elit. Aliquam eget bibendum dui. Nunc tristique, non dictum sollicitudin, metus mauris malesuada diam.</p>
    <ul class="bullets body">
      <li><svg class="bullet-icon"><use href="#icon-bullet"/></svg><span>Lorem ipsum dolor sit amet, consectetur adipiscing elit. Aliquam eget bibendum dui libero.</span></li>
      <li><svg class="bullet-icon"><use href="#icon-bullet"/></svg><span>Lorem ipsum dolor sit amet, consectetur adipiscing elit. Aliquam eget bibendum dui libero.</span></li>
      <li><svg class="bullet-icon"><use href="#icon-bullet"/></svg><span>Lorem ipsum dolor sit amet, consectetur adipiscing elit. Aliquam eget bibendum dui libero.</span></li>
      <li><svg class="bullet-icon"><use href="#icon-bullet"/></svg><span>Lorem ipsum dolor sit amet, consectetur adipiscing elit. Aliquam eget bibendum dui libero.</span></li>
    </ul>
  </div>
  <footer class="slide-footer"><span class="deck-title">PRESENTATION TITLE</span><span class="deck-sub">Presentation Subtitle</span><span class="page-no">2</span></footer>
</section>

<!-- 4 team -->
<section class="slide col-1 row-2">
  <header class="slide-header">Meet the team</header>
  <div class="brand-box">HALCYON</div>
  <div class="team">
    <div class="member">
      <div class="picture-box" role="img" aria-label="Team member portrait placeholder"><svg viewBox="0 0 40 32"><use href="#icon-image"/></svg></div>
      <p class="heading">Name here</p><p class="role">Job title</p>
      <p class="body">Lorem ipsum dolor sit amet, consectetur adipiscing elit. Aliquam eget bibendum dui libero in ante.</p>
    </div>
    <div class="member">
      <div class="picture-box" role="img" aria-label="Team member portrait placeholder"><svg viewBox="0 0 40 32"><use href="#icon-image"/></svg></div>
      <p class="heading">Name here</p><p class="role">Job title</p>
      <p class="body">Lorem ipsum dolor sit amet, consectetur adipiscing elit. Aliquam eget bibendum dui libero in ante.</p>
    </div>
    <div class="member">
      <div class="picture-box" role="img" aria-label="Team member portrait placeholder"><svg viewBox="0 0 40 32"><use href="#icon-image"/></svg></div>
      <p class="heading">Name here</p><p class="role">Job title</p>
      <p class="body">Lorem ipsum dolor sit amet, consectetur adipiscing elit. Aliquam eget bibendum dui libero in ante.</p>
    </div>
  </div>
  <footer class="slide-footer"><span class="deck-title">PRESENTATION TITLE</span><span class="deck-sub">Presentation Subtitle</span><span class="page-no">3</span></footer>
</section>

<!-- 5 two columns -->
<section class="slide col-2 row-2">
  <header class="slide-header">Two columns</header>
  <div class="brand-box">HALCYON</div>
  <div class="two-col">
    <div>
      <p class="heading">Title here</p>
      <p class="sub">Subtitle here</p>
      <p class="body">Lorem ipsum dolor sit amet, consectetur adipiscing elit. Suspendisse vitae sapien. Nam dapibus augue non sem placerat lacinia. Pellentesque augue odio, vulputate a purus vitae, semper mattis diam. Morbi consectetur pulvinar adipiscing. Sed in metus vitae urna.</p>
      <p class="note">Important notes here. Lorem ipsum dolor sit amet, consectetur adipiscing elit.</p>
      <p class="body">Maecenas mollis tempor nibh non laoreet. Curabitur malesuada, urna in volutpat pulvinar, massa mauris feugiat turpis, a aliquet urna magna non diam. Sed eu tempor nibh aenean.</p>
    </div>
    <div>
      <p class="body">Lorem ipsum dolor sit amet, consectetur adipiscing elit. Aliquam eget bibendum dui. Nunc tristique, non dictum sollicitudin, metus mauris diam.</p>
      <p class="sub">Subtitle here</p>
      <p class="body" style="margin-bottom:6px">Lorem ipsum dolor sit amet, consectetur adipiscing elit. Aliquam eget bibendum dui libero in ante lacus, quis mollis odio diam.</p>
      <ul class="bullets body">
        <li><svg class="bullet-icon"><use href="#icon-bullet"/></svg><span>Lorem ipsum dolor sit amet, consectetur adipiscing elit. Aliquam eget bibendum dui.</span></li>
        <li><svg class="bullet-icon"><use href="#icon-bullet"/></svg><span>Lorem ipsum dolor sit amet, consectetur adipiscing elit. Aliquam eget bibendum dui.</span></li>
        <li><svg class="bullet-icon"><use href="#icon-bullet"/></svg><span>Lorem ipsum dolor sit amet, consectetur adipiscing elit. Aliquam eget bibendum dui.</span></li>
        <li><svg class="bullet-icon"><use href="#icon-bullet"/></svg><span>Lorem ipsum dolor sit amet, consectetur adipiscing elit. Aliquam eget bibendum dui.</span></li>
      </ul>
    </div>
  </div>
  <footer class="slide-footer"><span class="deck-title">PRESENTATION TITLE</span><span class="deck-sub">Presentation Subtitle</span><span class="page-no">4</span></footer>
</section>

<!-- 6 one column -->
<section class="slide col-3 row-2">
  <header class="slide-header">One column</header>
  <div class="brand-box">HALCYON</div>
  <div class="one-col">
    <p class="heading">Title here</p>
    <p class="sub">Subtitle here</p>
    <p class="body">Lorem ipsum dolor sit amet, consectetur adipiscing elit. Fusce et diam vitae mi viverra vulputate. Suspendisse tempus in tortor vitae egestas. Nam dapibus augue non sem placerat lacinia. Pellentesque augue odio, vulputate a purus vitae, semper mollis diam. Morbi consectetur pulvinar elit nec tempus.</p>
    <p class="note">Important notes here. Lorem ipsum dolor sit amet, consectetur adipiscing elit.</p>
    <p class="body">Maecenas mollis tempor nibh non laoreet. Curabitur malesuada, urna in volutpat pulvinar, massa mauris feugiat turpis, a aliquet urna magna non diam. Sed eu tempor nibh. Aenean lacinia dolor lectus, vitae laoreet tortor mattis quis nunc.</p>
    <p class="sub" style="margin-top:8px">Subtitle here</p>
    <ul class="bullets body">
      <li><svg class="bullet-icon"><use href="#icon-bullet"/></svg><span>Lorem ipsum dolor sit amet, consectetur adipiscing elit. Aliquam eget bibendum dui libero in ante.</span></li>
      <li><svg class="bullet-icon"><use href="#icon-bullet"/></svg><span>Lorem ipsum dolor sit amet, consectetur adipiscing elit. Aliquam eget bibendum dui libero in ante.</span></li>
      <li><svg class="bullet-icon"><use href="#icon-bullet"/></svg><span>Lorem ipsum dolor sit amet, consectetur adipiscing elit. Aliquam eget bibendum dui libero in ante.</span></li>
    </ul>
  </div>
  <footer class="slide-footer"><span class="deck-title">PRESENTATION TITLE</span><span class="deck-sub">Presentation Subtitle</span><span class="page-no">5</span></footer>
</section>

<!-- 7 chart -->
<section class="slide col-1 row-3">
  <header class="slide-header">Sample chart slide</header>
  <div class="brand-box">HALCYON</div>
  <svg class="chart" viewBox="0 0 100 100" role="img" aria-label="Donut chart of four series">
    <g transform="rotate(-90 50 50)" fill="none" stroke-width="24">
      <circle cx="50" cy="50" r="38" stroke="var(--navy)" stroke-dasharray="148 238.8"/>
      <circle cx="50" cy="50" r="38" stroke="var(--sky)" stroke-dasharray="52.5 238.8" stroke-dashoffset="-148"/>
      <circle cx="50" cy="50" r="38" stroke="var(--green)" stroke-dasharray="21.5 238.8" stroke-dashoffset="-200.5"/>
      <circle cx="50" cy="50" r="38" stroke="var(--purple)" stroke-dasharray="16.8 238.8" stroke-dashoffset="-222"/>
    </g>
  </svg>
  <ul class="legend">
    <li><span class="swatch" style="background:var(--navy)"></span><p class="series">Serie 1</p><p class="body">Lorem ipsum dolor sit amet, consectetur adipiscing elit. Aliquam eget bibendum dui.</p></li>
    <li><span class="swatch" style="background:var(--sky)"></span><p class="series">Serie 1</p><p class="body">Lorem ipsum dolor sit amet, consectetur adipiscing elit. Aliquam eget bibendum dui.</p></li>
    <li><span class="swatch" style="background:var(--green)"></span><p class="series">Serie 1</p><p class="body">Lorem ipsum dolor sit amet, consectetur adipiscing elit. Aliquam eget bibendum dui.</p></li>
    <li><span class="swatch" style="background:var(--purple)"></span><p class="series">Serie 1</p><p class="body">Lorem ipsum dolor sit amet, consectetur adipiscing elit. Aliquam eget bibendum dui.</p></li>
  </ul>
  <footer class="slide-footer"><span class="deck-title">PRESENTATION TITLE</span><span class="deck-sub">Presentation Subtitle</span><span class="page-no">6</span></footer>
</section>

<!-- 8 testimonial -->
<section class="slide col-2 row-3">
  <header class="slide-header">Testimonial client</header>
  <div class="brand-box">HALCYON</div>
  <div class="testimonial-main">
    <div class="picture-box" role="img" aria-label="Featured client photo placeholder"><svg viewBox="0 0 40 32" style="width:22%"><use href="#icon-image"/></svg></div>
    <p class="heading">Name here</p>
    <p class="body">Lorem ipsum dolor sit amet, consectetur adipiscing elit. Aliquam eget bibendum dui. Nunc tristique, non dictum sollicitudin, metus mauris malesuada diam, quis mollis odio libero in ante. Quisque eget enim nec purus pellentesque viverra. Nam sit amet dui accumsan, mattis enim ut, venenatis mauris. Sed iaculis ante eu eros pellentesque.</p>
  </div>
  <div class="testimonial-list">
    <div class="testimonial-item">
      <div class="picture-box" role="img" aria-label="Client photo placeholder"><svg viewBox="0 0 40 32" style="width:44%"><use href="#icon-image"/></svg></div>
      <div><p class="heading">Name here</p><p class="role">Job title</p><p class="body">Lorem ipsum dolor sit amet, consectetur adipiscing elit. Aliquam eget bibendum.</p></div>
    </div>
    <div class="testimonial-item">
      <div class="picture-box" role="img" aria-label="Client photo placeholder"><svg viewBox="0 0 40 32" style="width:44%"><use href="#icon-image"/></svg></div>
      <div><p class="heading">Name here</p><p class="role">Job title</p><p class="body">Lorem ipsum dolor sit amet, consectetur adipiscing elit. Aliquam eget bibendum.</p></div>
    </div>
    <div class="testimonial-item">
      <div class="picture-box" role="img" aria-label="Client photo placeholder"><svg viewBox="0 0 40 32" style="width:44%"><use href="#icon-image"/></svg></div>
      <div><p class="heading">Name here</p><p class="role">Job title</p><p class="body">Lorem ipsum dolor sit amet, consectetur adipiscing elit. Aliquam eget bibendum.</p></div>
    </div>
  </div>
  <footer class="slide-footer"><span class="deck-title">PRESENTATION TITLE</span><span class="deck-sub">Presentation Subtitle</span><span class="page-no">7</span></footer>
</section>

<!-- 9 closing -->
<section class="slide col-3 row-3">
  <div class="closing-art" role="img" aria-label="Blue abstract background with soft light streaks"></div>
  <p class="closing-brand">HALCYON</p>
  <p class="closing-thanks">Thank<br>you</p>
  <span class="closing-divider"></span>
  <div class="closing-contact">
    <p class="web">http://halcyonhealth.example/</p>
    <p>418 Larkspur Lane, Cedar Hollow, TX 75100</p>
    <p class="mail">admin@halcyonhealth.example</p>
  </div>
</section>

</body>
</html>
```